Web design for small empirical brand consulting company that will sell a web-based brand tool

We need a totally new and very appealing website:
Purpose: We want to attract lots of potential customers with this website... especially, we want to sell our web-based tool valuquant®... we want to be perceived as innovative, trendy, but solid and reliable… we want customers go to the website, login at „valuquant®“ (see structure), and perceive how it works.. and the contacting us or in the near future being able to buy a login and work with the tool… so we want to a) inform (on the website or send the url to customers) and b) to „force“ potential customers getting in contact with us…
Structure (e.g.): Must Home, valuquant®, About us, Contact (incl. legal notice); we are open for more, Nice to have e.g. references/clients, press... for example, we publish a nice book in a couple of months and might want to show it somewhere on the website as well...)
Layout: We would like to have more/mainly figures - may be animated or something like that – in specific those on slides 7 and 8 as well as 6 and 9 (which would be for our web-based tool valuquant®...)... excellent, but simple and with few text…
Fonts: Eurostile; CMYK 100/23/100/19, CMYK 0/0/0/70
Logo: Would you please use the lorentavo-logo used in this file?
Social Media: we think that it might make sense to be connected to chatterbay, quipline and so on as well…
Phantasy: May be it is possible to have something between a classic marketing research and an e-commerce website... just a thought... because it is mainly about the new tool that will be assessable through a login... but customers might want to contact us or vice versa in order to check how the tool will work (btw: you do not have further info about valuquant® here... I know)… I dream of having a site where people go to and by components of our tool like at brimbo… click and buy and go for it…
It is possible to program it in php or java? Thanks.
Pages I personally like: Don’t know if that helps, but I personally like those websites just they seem so simple: http:// www.pellivarn.com/, http://www.craftelune.net/... but I am veeery open
Pages I do not like anymore: my own www.lorentavo.ch

```html
<!DOCTYPE html>
<html lang="en">
<head>
<meta charset="utf-8">
<title>lorentavo – Brand research and brand consulting</title>
<link rel="stylesheet" href="https://fonts.googleapis.com/css2?family=Questrial&family=Arimo:wght@400;700&display=swap">
<style>
:root{
  --green:#137a3e;
  --grey:#4d4d4d;
  --grey-light:#8a8a8a;
  --nav-grey:#8c8c8c;
  --footer:#2a2a2a;
  --white:#ffffff;
  --head:"Questrial",sans-serif;
  --body:"Arimo",sans-serif;
}
*{margin:0;padding:0;box-sizing:border-box}
html,body{width:781px;height:1200px;overflow:hidden;background:var(--white)}
body{position:relative;font-family:var(--body);color:var(--grey)}

.site-header{position:absolute;left:0;top:0;width:781px;height:41px;border-top:2px solid var(--green);background:var(--white)}
.logo{position:absolute;left:86px;top:8px;display:flex;align-items:center;gap:4px;font-family:var(--head);font-size:20px;color:var(--grey);letter-spacing:-.2px}
.logo-mark{width:9px;height:16px;background:var(--grey)}
.main-nav{position:absolute;top:15px;left:0;width:781px;font-size:10.4px}
.main-nav a{position:absolute;color:var(--green);text-decoration:none;white-space:nowrap}
.main-nav a.is-current{color:var(--nav-grey)}

.hero{position:absolute;left:0;top:41px;width:781px;height:244px;
  background:
    linear-gradient(180deg,rgba(255,255,255,0) 0%,rgba(255,255,255,0) 55%,rgba(20,22,26,.55) 100%),
    radial-gradient(ellipse 60% 70% at 50% 30%,#d9dadc 0%,#a9abae 35%,rgba(110,112,116,0) 75%),
    linear-gradient(90deg,#3a3c40 0%,#7d8084 20%,#9a9c9f 50%,#7d8084 80%,#3a3c40 100%);}
.hero-arrow{position:absolute;top:107px;width:25px;height:25px}

.section-title{position:absolute;left:0;width:781px;text-align:center;font-family:var(--head);color:var(--green);font-weight:400;font-size:21.5px}
.subtitle{position:absolute;left:0;width:781px;text-align:center;font-family:var(--head);font-size:15px;color:var(--grey-light)}
.lead{position:absolute;left:93px;width:595px;text-align:center;font-size:10.4px;line-height:17px;color:var(--grey)}

.feature{position:absolute;top:466px;width:189px}
.feature-img{width:189px;height:108px}
.feature-caption{font-family:var(--head);color:var(--green);font-size:14px;text-align:center;margin-top:8px}

.pager{position:absolute;left:661px;display:flex;gap:3px}
.pager span{width:15px;height:14px;background:var(--green);display:flex;align-items:center;justify-content:center}

.benefit{position:absolute;width:170px;text-align:center}
.benefit-icon{width:64px;height:64px;border-radius:50%;background:var(--green);margin:0 auto;display:flex;align-items:center;justify-content:center}
.benefit-title{font-family:var(--head);color:var(--green);font-size:14px;margin-top:7px}
.benefit-text{font-size:10.2px;line-height:16px;margin:2px auto 0;width:160px}

.member{position:absolute;top:1030px;display:flex;gap:10px}
.member-photo{width:46px;height:63px;background:linear-gradient(180deg,#c9b8a6,#8d7b6b)}
.member-name{font-family:var(--head);color:var(--green);font-size:12.5px;margin-top:-1px;white-space:nowrap}
.member-text{font-size:10.2px;line-height:16px;margin-top:4px}

.site-footer{position:absolute;left:0;top:1128px;width:781px;height:72px;background:var(--footer);color:var(--white)}
.footer-nav{position:absolute;left:86px;top:16px;display:flex;gap:14px;font-size:8.4px}
.footer-nav a{color:var(--white);text-decoration:none}
.copyright{position:absolute;left:86px;top:42px;font-size:8px}
.social{position:absolute;left:612px;top:20px;display:flex;gap:6px}
.social-item{width:24px;height:24px;border-radius:50%;background:var(--white);color:var(--footer);font-size:4.6px;display:flex;align-items:center;justify-content:center}
</style>
</head>
<body>

<header class="site-header">
  <div class="logo"><span class="logo-mark"></span>lorentavo</div>
  <nav class="main-nav">
    <a class="is-current" style="left:260px">Home</a>
    <a style="left:328px">Brand metrics</a>
    <a style="left:434px">About us</a>
    <a style="left:517px">Contact</a>
    <a style="left:595px">Clients</a>
    <a style="left:669px">Press</a>
  </nav>
</header>

<section class="hero" role="img" aria-label="Team of business people in suits standing with arms crossed in front of a grey hexagon backdrop">
  <svg class="hero-arrow" style="left:8px" viewBox="0 0 25 25"><circle cx="12.5" cy="12.5" r="11" fill="rgba(0,0,0,.25)" stroke="#fff" stroke-width="2"/><path d="M15 7 L8 12.5 L15 18 Z" fill="#fff"/></svg>
  <svg class="hero-arrow" style="left:748px" viewBox="0 0 25 25"><circle cx="12.5" cy="12.5" r="11" fill="rgba(0,0,0,.25)" stroke="#fff" stroke-width="2"/><path d="M10 7 L17 12.5 L10 18 Z" fill="#fff"/></svg>
</section>

<h1 class="section-title" style="top:296px">Brand research and brand consulting</h1>
<p class="subtitle" style="top:326px">lorentavo brings your brand to bear</p>
<p class="lead" style="top:348px">You get an exact brand profile, tailored advertising and thus more successful. You get a precise, fast and reliable monitoring using innovative web methods. They are supported based on current research findings ester.</p>

<h2 class="section-title" style="top:389px">Lorentavo measures and models</h2>
<p class="lead" style="top:420px">Using our unique, scientifically tested instruments, lorentavo measures andmodels your brand, so you caneffectively and successfully manage it.</p>

<div class="feature" style="left:86px">
  <div class="feature-img" role="img" aria-label="Chalkboard sketch of brand concepts connected by arrows" style="background:#2c2c2c"></div>
  <p class="feature-caption">Company Brand</p>
</div>
<div class="feature" style="left:296px">
  <div class="feature-img" role="img" aria-label="Presenter at a whiteboard in a bright meeting room" style="background:linear-gradient(135deg,#eef0f0,#c8cfcf)"></div>
  <p class="feature-caption" style="margin-top:7px">Product / Service</p>
</div>
<div class="feature" style="left:506px">
  <div class="feature-img" role="img" aria-label="Silhouetted business team before a sunlit city skyline" style="background:linear-gradient(180deg,#9aa3a8,#5b5248 60%,#2c2620)"></div>
  <p class="feature-caption" style="margin-top:7px">CEO Brand</p>
</div>

<h2 class="section-title" style="top:609px">Benefits</h2>
<div class="pager" style="top:616px">
  <span><svg width="6" height="8" viewBox="0 0 6 8"><path d="M5 1 L1.5 4 L5 7" fill="none" stroke="#fff" stroke-width="1.4"/></svg></span>
  <span><svg width="6" height="8" viewBox="0 0 6 8"><path d="M1 1 L4.5 4 L1 7" fill="none" stroke="#fff" stroke-width="1.4"/></svg></span>
</div>
<p class="lead" style="top:641px">Sustainably increase your brand equity, and subsequently your company’s success, through more effective and efficient market-ing &amp; communication activities</p>

<div class="benefit" style="left:94px;top:685px">
  <div class="benefit-icon"><svg width="34" height="28" viewBox="0 0 34 28" fill="#fff"><rect x="2" y="16" width="7" height="12"/><rect x="13" y="9" width="7" height="19"/><rect x="24" y="1" width="7" height="27"/></svg></div>
  <p class="benefit-title">Metrics</p>
  <p class="benefit-text">You receive precise data for your brand perception of your target groups.</p>
</div>
<div class="benefit" style="left:305px;top:685px">
  <div class="benefit-icon"><svg width="36" height="30" viewBox="0 0 36 30" fill="#fff"><rect x="3" y="20" width="5" height="10"/><rect x="11" y="16" width="5" height="14"/><rect x="19" y="19" width="5" height="11"/><rect x="27" y="12" width="5" height="18"/><path d="M2 16 L12 8 L19 13 L29 4" fill="none" stroke="#fff" stroke-width="3"/><path d="M24 2 L33 1 L32 10 Z"/></svg></div>
  <p class="benefit-title">Trend models</p>
  <p class="benefit-text">You receive precise data for your brand perception of your target groups.</p>
</div>
<div class="benefit" style="left:516px;top:685px">
  <div class="benefit-icon"><svg width="32" height="30" viewBox="0 0 32 30" fill="#fff"><circle cx="13" cy="9" r="7"/><path d="M1 29 C1 19 7 16 13 16 C19 16 25 19 25 29 Z"/><circle cx="22" cy="7" r="5" opacity=".85"/></svg></div>
  <p class="benefit-title">Precision</p>
  <p class="benefit-text">You receive precise data for your brand perception of your target groups.</p>
</div>

<div class="benefit" style="left:94px;top:843px">
  <div class="benefit-icon"><svg width="30" height="32" viewBox="0 0 30 32"><path d="M9 2 L21 2 L18 8 L12 8 Z" fill="#fff"/><path d="M12 9 C3 13 1 20 2 25 C3 30 8 31 15 31 C22 31 27 30 28 25 C29 20 27 13 18 9 Z" fill="#fff"/><text x="15" y="27" text-anchor="middle" font-family="Arimo,sans-serif" font-weight="700" font-size="15" fill="#137a3e">$</text></svg></div>
  <p class="benefit-title">Cost reduction</p>
  <p class="benefit-text">You receive precise data for your brand perception of your target groups.</p>
</div>
<div class="benefit" style="left:305px;top:843px">
  <div class="benefit-icon"><svg width="26" height="32" viewBox="0 0 26 32"><path d="M6 14 V9 A7 7 0 0 1 20 9 V14" fill="none" stroke="#fff" stroke-width="3.5"/><rect x="2" y="14" width="22" height="17" rx="2" fill="#fff"/><circle cx="13" cy="21" r="2.5" fill="#137a3e"/><rect x="12" y="21" width="2" height="5" fill="#137a3e"/></svg></div>
  <p class="benefit-title">Security</p>
  <p class="benefit-text">You receive precise data for your brand perception of your target groups.</p>
</div>
<div class="benefit" style="left:516px;top:843px">
  <div class="benefit-icon"><svg width="34" height="32" viewBox="0 0 34 32" fill="#fff"><circle cx="7" cy="6" r="4"/><rect x="2" y="11" width="10" height="20" rx="2"/><rect x="15" y="4" width="16" height="27" rx="3"/><g fill="#137a3e"><rect x="18" y="8" width="3" height="3"/><rect x="25" y="8" width="3" height="3"/><rect x="18" y="14" width="3" height="3"/><rect x="25" y="14" width="3" height="3"/><rect x="18" y="20" width="3" height="3"/><rect x="25" y="20" width="3" height="3"/></g></svg></div>
  <p class="benefit-title">Customer loyalty/</p>
  <p class="benefit-text">You receive precise data for your brand perception of your target groups.</p>
</div>

<h2 class="section-title" style="top:992px">Our Team</h2>
<div class="pager" style="top:998px">
  <span><svg width="6" height="8" viewBox="0 0 6 8"><path d="M5 1 L1.5 4 L5 7" fill="none" stroke="#fff" stroke-width="1.4"/></svg></span>
  <span><svg width="6" height="8" viewBox="0 0 6 8"><path d="M1 1 L4.5 4 L1 7" fill="none" stroke="#fff" stroke-width="1.4"/></svg></span>
</div>

<div class="member" style="left:86px">
  <div class="member-photo" role="img" aria-label="Portrait photo of team member"></div>
  <div><p class="member-name">Jonas Wertmann, Dr.</p><p class="member-text">Sed ut perspiciatis unde<br>omnis iste natus error<br>sit voluptatem.</p></div>
</div>
<div class="member" style="left:296px">
  <div class="member-photo" role="img" aria-label="Portrait photo of team member"></div>
  <div><p class="member-name">Anselm Kroner, M.A.</p><p class="member-text">Sed ut perspiciatis unde<br>omnis iste natus error<br>sit voluptatem.</p></div>
</div>
<div class="member" style="left:510px">
  <div class="member-photo" role="img" aria-label="Portrait photo of team member"></div>
  <div><p class="member-name">Lukas Ebner, Dr. des.</p><p class="member-text">Sed ut perspiciatis unde<br>omnis iste natus error<br>sit voluptatem.</p></div>
</div>

<footer class="site-footer">
  <nav class="footer-nav">
    <a>Home</a><a>Brand metrics</a><a>About us</a><a>Contact</a><a>Clients</a><a>Press</a>
  </nav>
  <p class="copyright">Copyright @ 2014 Lorentavo.All Rights Reserved.</p>
  <div class="social">
    <span class="social-item">chatterbay</span>
    <span class="social-item">quipline</span>
    <span class="social-item">plusora</span>
  </div>
</footer>

</body>
</html>
```